Lotus Market Hall VIP Card(Magnetic strip plastic card)

We need Fancy,Simple,VIP customer card design for a grocery store name"Lotus Market Hall", Chinese name"福润商场“.Major color should be Dark red. This design is based on a VIP gift card project, which means design should consider about the back side with magnetic strip area and mostly it will be plastic material.

Target Market(s)

Rich Customers

Industry/Entity Type

Grocery Store

Contact Information for Business Card

People actually put more than $1000 into the card for shopping

Font styles to use
Serif
Sans Serif
Decorative
Script
Other font styles liked:
• Fancy

Colors
ec1f27
fbed22

Requirements
Must have
• Red color
Nice to have
• Better logo transformation.

```html
<!DOCTYPE html>
<html lang="en">
<head>
<meta charset="UTF-8">
<title>Lotus Market Hall – VIP Card</title>
<link rel="stylesheet" href="https://fonts.googleapis.com/css2?family=Open+Sans:wght@400;700&family=Noto+Serif+SC:wght@600&display=swap">
<style>
  :root {
    --stage: #1b1b1b;
    --card-white: #f6f3f0;
    --wine-light: #9e1a22;
    --wine-dark: #5e0b12;
    --band-wine: #7d121a;
    --red: #ec1f27;
    --gold: #fbed22;
    --gold-soft: #e9cf4a;
    --strip: #141414;
    --text-white: #ffffff;
  }
  * { margin: 0; padding: 0; box-sizing: border-box; }
  html, body { width: 1200px; height: 864px; overflow: hidden; }
  body {
    background: var(--stage);
    font-family: "Open Sans", Arial, sans-serif;
    position: relative;
  }
  .card {
    position: absolute;
    width: 540px;
    height: 320px;
    border-radius: 22px;
    overflow: hidden;
    top: 272px;
  }

  /* ---------- Back face ---------- */
  .card-back { left: 610px; background: var(--card-white); }
  .magnetic-strip {
    position: absolute;
    left: 0; right: 0; top: 24px;
    height: 48px;
    background: var(--strip);
  }
  .card-back .band {
    position: absolute;
    height: 56px;
    background: var(--band-wine);
  }
  .card-back .band-left { left: 0; top: 100px; width: 150px; }
  .card-back .band-right { right: 0; top: 232px; width: 150px; }
  .dot {
    position: absolute;
    border-radius: 50%;
    background: var(--red);
  }
  .card-back .dot-left { width: 68px; height: 68px; left: 76px; top: 94px; }
  .card-back .dot-right { width: 68px; height: 68px; right: 76px; top: 226px; }
  .brand-mark {
    position: absolute;
    display: flex;
    align-items: center;
    gap: 12px;
    font-weight: 700;
    white-space: nowrap;
  }
  .brand-mark .mark-circle {
    border-radius: 50%;
    flex: none;
  }
  .card-back .brand-mark {
    left: 50%; top: 196px;
    transform: translate(-50%, -50%);
    font-size: 28px;
    color: var(--wine-dark);
  }
  .card-back .brand-mark .mark-circle { width: 30px; height: 30px; background: var(--wine-dark); }

  /* ---------- Front face ---------- */
  .card-front {
    left: 50px;
    background: radial-gradient(ellipse at 45% 35%, var(--wine-light), var(--wine-dark) 95%);
  }
  .card-front .brand-mark {
    left: 26px; top: 40px;
    font-size: 17px;
    gap: 8px;
    color: var(--gold);
  }
  .card-front .brand-mark .mark-circle { width: 20px; height: 20px; background: var(--gold); }
  .holder {
    position: absolute;
    right: 134px; top: 24px;
    text-align: right;
  }
  .holder-name { color: var(--text-white); font-weight: 700; font-size: 22px; line-height: 1.2; }
  .holder-title { color: var(--gold-soft); font-weight: 700; font-size: 12px; }
  .white-tab {
    position: absolute;
    background: var(--card-white);
    width: 100px; height: 80px;
  }
  .tab-top { right: 0; top: 22px; }
  .tab-bottom { left: 0; top: 190px; }
  .card-front .dot-top { width: 72px; height: 72px; right: 38px; top: 26px; }
  .card-front .dot-bottom { width: 72px; height: 72px; left: 30px; top: 194px; }
  .hero-name {
    position: absolute;
    left: 0; right: 0; top: 90px;
    text-align: center;
    font-family: "Noto Serif SC", serif;
    font-weight: 600;
    font-size: 88px;
    letter-spacing: 36px;
    padding-left: 36px;
    color: var(--gold);
    line-height: 1;
  }
  .contacts {
    position: absolute;
    left: 122px; top: 206px;
    list-style: none;
    color: var(--text-white);
    font-size: 14px;
  }
  .contacts li { display: flex; align-items: center; gap: 12px; height: 25px; }
  .contacts svg { width: 14px; height: 14px; flex: none; }
  .vip-label {
    position: absolute;
    right: 28px; bottom: 22px;
    color: var(--gold);
    font-weight: 700;
    font-size: 20px;
    letter-spacing: 4px;
  }
</style>
</head>
<body>

  <section class="card card-front" aria-label="Card front">
    <div class="brand-mark"><span class="mark-circle"></span>Lotus Market Hall</div>

    <div class="white-tab tab-top"></div>
    <div class="dot dot-top"></div>
    <div class="holder">
      <p class="holder-name">Mara Quinn</p>
      <p class="holder-title">Business Director</p>
    </div>

    <p class="hero-name" lang="zh">福润</p>

    <div class="white-tab tab-bottom"></div>
    <div class="dot dot-bottom"></div>

    <ul class="contacts">
      <li>
        <svg viewBox="0 0 14 14" fill="none" stroke="#fbed22" stroke-width="1.3"><rect x="3.5" y="1" width="7" height="12" rx="1.2"/><line x1="6" y1="11" x2="8" y2="11"/></svg>
        0491 570 156
      </li>
      <li>
        <svg viewBox="0 0 14 14" fill="none" stroke="#fbed22" stroke-width="1.3"><rect x="1" y="3" width="12" height="8.5"/><polyline points="1,3 7,8 13,3"/></svg>
        mara@lotusmarkethall.com.au
      </li>
      <li>
        <svg viewBox="0 0 14 14" fill="none" stroke="#fbed22" stroke-width="1.2"><circle cx="7" cy="7" r="5.8"/><ellipse cx="7" cy="7" rx="2.5" ry="5.8"/><line x1="1.2" y1="7" x2="12.8" y2="7"/></svg>
        www.lotusmarkethall.com.au
      </li>
    </ul>

    <p class="vip-label">VIP</p>
  </section>

  <section class="card card-back" aria-label="Card back">
    <div class="magnetic-strip"></div>
    <div class="band band-left"></div>
    <div class="dot dot-left"></div>
    <div class="band band-right"></div>
    <div class="dot dot-right"></div>
    <div class="brand-mark"><span class="mark-circle"></span>Lotus Market Hall</div>
  </section>

</body>
</html>
```